indépendant en tant que Massothérapeute et Préparateur Mental, j'ai besoin de ...

Massothérapeute et préparateur mental indépendant, je recherche une carte de visite sobre et dynamique, sans images liées au massage ou à la préparation mentale mais intégrant mon logo. Les couleurs que j'aime bien sont : Blanc, gris, anthracite, noir et jaune

Contact Information for Business Card

carte de préférence Horizontale
neutre qui puisse toucher le deux domaines Massothérapie et préparation mentale

Requirements
Must have
• mon projet doit intégrer au recto:
LOGO
Loïc Bardèze
078 513 26 48
info@loicbardeze.ch
et éventuellement www.loicbardeze.ch

et au verso les deux adresses:

Chemin des Ormilles 7B
1400 Yverdon-les-Bains

Route de la Gravière 9
1700 Fribourg

Should not have
• mon projet ne doit pas contenir d'image en liens avec le massage ni la préparation mentale.

```html
<!DOCTYPE html>
<html lang="fr">
<head>
<meta charset="utf-8">
<title>Loïc Bardèze – Cartes de visite</title>
<link href="https://fonts.googleapis.com/css2?family=Montserrat:wght@500;600;700&family=Arimo:wght@400&display=swap" rel="stylesheet">
<style>
  :root {
    --backdrop: #1c1c1c;
    --card: #0b0b0b;
    --white: #f2f2f2;
    --grey: #b9b9b9;
    --rule: #5a5a5a;
  }
  * { box-sizing: border-box; margin: 0; padding: 0; }
  html, body { width: 1200px; height: 900px; overflow: hidden; }
  body {
    background: var(--backdrop);
    display: flex;
    flex-direction: column;
    align-items: center;
    justify-content: center;
    gap: 60px;
    font-family: "Arimo", Arial, sans-serif;
  }
  .card {
    position: relative;
    width: 620px;
    height: 354px;
    background: var(--card);
    box-shadow: 0 12px 30px rgba(0,0,0,.55);
  }
  .brand {
    position: absolute;
    display: flex;
    align-items: center;
    gap: 16px;
  }
  .brand-dot {
    width: 54px; height: 54px;
    border-radius: 50%;
    background: var(--white);
    flex: none;
  }
  .brand-name {
    font-family: "Montserrat", sans-serif;
    font-weight: 600;
    font-size: 30px;
    color: var(--white);
    line-height: 1;
  }
  .brand-role {
    font-family: "Montserrat", sans-serif;
    font-weight: 500;
    font-size: 11px;
    letter-spacing: .06em;
    font-variant: small-caps;
    color: var(--white);
    margin-top: 6px;
  }
  .card-front .brand { left: 150px; top: 86px; }
  .holder {
    position: absolute;
    left: 60px; bottom: 70px;
    font-family: "Montserrat", sans-serif;
    font-weight: 700;
    font-size: 24px;
    letter-spacing: .02em;
    color: var(--white);
  }
  .divider {
    position: absolute;
    width: 1px;
    background: var(--rule);
  }
  .card-front .divider { left: 330px; top: 198px; height: 90px; }
  .contact-list {
    position: absolute;
    left: 352px; top: 198px;
    list-style: none;
    display: flex;
    flex-direction: column;
    gap: 8px;
    font-size: 21px;
    color: var(--grey);
  }
  .contact-list li { display: flex; align-items: center; gap: 8px; }
  .contact-list svg { width: 16px; height: 16px; flex: none; }
  .card-back .brand { left: 120px; top: 70px; }
  .card-back .divider { left: 318px; top: 200px; height: 66px; }
  .address {
    position: absolute;
    top: 200px;
    font-size: 20px;
    line-height: 1.3;
    color: var(--grey);
  }
  .address-fribourg { right: 320px; text-align: right; }
  .address-yverdon { left: 338px; }
</style>
</head>
<body>

<section class="card card-front" aria-label="Recto">
  <div class="brand">
    <span class="brand-dot"></span>
    <div>
      <div class="brand-name">Loïc Bardèze</div>
      <div class="brand-role">Massothérapeute / Préparateur Mental</div>
    </div>
  </div>
  <p class="holder">LOÏC BARDÈZE</p>
  <span class="divider"></span>
  <ul class="contact-list">
    <li>
      <svg viewBox="0 0 16 16" aria-hidden="true"><path d="M4 1.5l2.2 3-1.4 1.6c.8 1.8 2.3 3.3 4.1 4.1l1.6-1.4 3 2.2-1.3 2.6C6.6 13.4 2.6 9.4 1.4 3z" fill="#e6e6e6"/></svg>
      078 513 26 48
    </li>
    <li>
      <svg viewBox="0 0 16 16" aria-hidden="true"><rect x="1" y="3" width="14" height="10" fill="#e6e6e6"/><path d="M1 3l7 6 7-6" fill="none" stroke="#0b0b0b" stroke-width="1.2"/></svg>
      info@loicbardeze.ch
    </li>
    <li>
      <svg viewBox="0 0 16 16" aria-hidden="true"><g fill="none" stroke="#e6e6e6" stroke-width="1.3"><circle cx="8" cy="8" r="6.5"/><ellipse cx="8" cy="8" rx="3" ry="6.5"/><path d="M1.5 8h13M2.5 4.5h11M2.5 11.5h11"/></g></svg>
      www.loicbardeze.ch
    </li>
  </ul>
</section>

<section class="card card-back" aria-label="Verso">
  <div class="brand">
    <span class="brand-dot"></span>
    <div>
      <div class="brand-name">Loïc Bardèze</div>
      <div class="brand-role">Massothérapeute / Préparateur Mental</div>
    </div>
  </div>
  <address class="address address-fribourg">Route de la Gravière 9<br>1700 Freiburg</address>
  <span class="divider"></span>
  <address class="address address-yverdon">Chemin des Ormilles 7B<br>1400 Yverdon-les-Bains</address>
</section>

</body>
</html>
```